BrivoTerna. Lantern of the Steady Harvest. Business card

Professional business card for BrivoTerna (Lantern of the Steady Harvest)
My rationale: Strategy-> Execution-> Results-> Value that lead to the BrivoTerna name: We put the Lantern of the Steady Harvest.
We deliver value to our customers helping them at defining a good strategy (cyan arrow). 90% of well formulated strategies fail due to poor execution so we also consider strategical execution very important (green arrow). Due to the execution we obtain the results (blue arrow). Finally, the results provide feedback to redefine strategy, and the new strategy has to be executed and new results obtained providing new feedback and on and on. It's like a wheel that finally, must create corporate value: value for shareholders, staholders, employees, providers...-

Target Market(s)

CEOs and steering comitees , invewrnent funds

Industry/Entity Type

Business Consultant

Contact Information for Business Card

Teodoro Vinsquel
CEO & Founder
teodoro.vinsquel@brivoterna-example.com
Mobile: +34 655.803.912
www.brivoterna-example.com

Colors

Designer to choose colors to be used in the design.

Requirements
Nice to have
• Nice to hace the words: Strategy, execution, results
• Nice to vave the claim: Lantern of the Steady Harvest
• The three colors should be shown:
• cyan for STRATEGY
• green for EXECUTION
• blue for RESULTS
Should not have
• Complete black background

```html
<!DOCTYPE html>
<html lang="en">
<head>
<meta charset="utf-8">
<title>BrivoTerna — Business Card</title>
<link rel="stylesheet" href="https://fonts.googleapis.com/css2?family=Open+Sans:wght@400;600;700;800&display=swap">
<style>
  :root {
    --navy: #253c8c;
    --green: #9bc93c;
    --cyan: #27aee3;
    --white: #ffffff;
    --ink: #1f2a44;
    --stage: #e9ebef;
  }
  * { box-sizing: border-box; margin: 0; padding: 0; }
  html, body {
    width: 1200px; height: 900px; overflow: hidden;
    background: var(--stage);
    font-family: "Open Sans", Arial, sans-serif;
  }
  .sheet {
    width: 1200px; height: 900px;
    display: flex; flex-direction: column; align-items: center; justify-content: center;
    gap: 40px;
  }
  .card {
    position: relative;
    width: 630px; height: 360px;
    overflow: hidden;
    box-shadow: 0 6px 20px rgba(20, 30, 60, 0.18);
  }

  /* Front */
  .card--front { background: var(--navy); color: var(--white); }
  .front-brand {
    position: absolute; left: 0; right: 0; top: 128px;
    display: flex; align-items: center; justify-content: center; gap: 16px;
  }
  .brand-dot { width: 26px; height: 26px; border-radius: 50%; background: var(--white); }
  .front-name { font-size: 56px; font-weight: 700; letter-spacing: -1px; line-height: 1; }
  .pillars {
    position: absolute; left: 0; right: 0; bottom: 0;
    display: grid; grid-template-columns: 31% 36% 33%;
  }
  .pillar { position: relative; height: 46px; }
  .pillar span {
    position: absolute; bottom: 16px;
    font-size: 15px; letter-spacing: 1.2px; font-weight: 400;
  }
  .pillar::after { content: ""; position: absolute; left: 0; right: 0; bottom: 0; height: 9px; }
  .pillar--strategy span { left: 72px; }
  .pillar--strategy::after { background: var(--white); }
  .pillar--execution span { left: 82px; }
  .pillar--execution::after { background: var(--green); }
  .pillar--results span { right: 74px; }
  .pillar--results::after { background: var(--cyan); }

  /* Back */
  .card--back { background: var(--white); color: var(--ink); }
  .back-brand {
    position: absolute; left: 44px; top: 30px;
    font-size: 58px; font-weight: 700; letter-spacing: -1.5px; color: var(--navy); line-height: 1;
  }
  .person { position: absolute; left: 50px; top: 114px; }
  .person-name { font-size: 24px; font-weight: 800; letter-spacing: 1.2px; color: var(--navy); text-transform: uppercase; line-height: 1.1; }
  .person-role { font-size: 16px; color: var(--green); line-height: 1.3; }
  .divider { position: absolute; left: 50px; right: 50px; top: 186px; height: 1.5px; background: var(--green); }
  .contacts { position: absolute; left: 50px; top: 204px; list-style: none; }
  .contacts li { display: flex; align-items: center; gap: 10px; font-size: 16px; line-height: 26px; color: var(--ink); }
  .contacts svg { width: 18px; height: 18px; flex: none; }
  .claim {
    position: absolute; left: 50px; top: 294px;
    font-size: 16px; letter-spacing: 0.6px; text-transform: uppercase; color: var(--ink);
  }
  .base-band {
    position: absolute; left: 0; right: 0; bottom: 0; height: 12px;
    display: grid; grid-template-columns: 36% 42% 22%;
  }
  .base-band i:nth-child(1) { background: var(--navy); }
  .base-band i:nth-child(2) { background: var(--green); }
  .base-band i:nth-child(3) { background: var(--cyan); }
</style>
</head>
<body>
<main class="sheet">

  <section class="card card--front" aria-label="Business card front">
    <div class="front-brand">
      <span class="brand-dot" aria-hidden="true"></span>
      <span class="front-name">BrivoTerna</span>
    </div>
    <div class="pillars">
      <div class="pillar pillar--strategy"><span>STRATEGY</span></div>
      <div class="pillar pillar--execution"><span>EXECUTION</span></div>
      <div class="pillar pillar--results"><span>RESULTS</span></div>
    </div>
  </section>

  <section class="card card--back" aria-label="Business card back">
    <div class="back-brand">BrivoTerna</div>
    <div class="person">
      <p class="person-name">Teodoro Vinsquel</p>
      <p class="person-role">CEO &amp; Founder</p>
    </div>
    <div class="divider"></div>
    <ul class="contacts">
      <li>
        <svg viewBox="0 0 24 24" fill="none" stroke="#27aee3" stroke-width="1.8" stroke-linecap="round" stroke-linejoin="round" aria-hidden="true">
          <path d="M6.6 3h3l1.5 4.5-2 1.3a11 11 0 0 0 6.1 6.1l1.3-2L21 14.4v3a2 2 0 0 1-2.2 2A17 17 0 0 1 4.6 5.2 2 2 0 0 1 6.6 3z"/>
        </svg>
        +34 655.803.912
      </li>
      <li>
        <svg viewBox="0 0 24 24" fill="none" stroke="#27aee3" stroke-width="1.8" stroke-linejoin="round" aria-hidden="true">
          <rect x="3" y="5.5" width="18" height="13" rx="1"/>
          <path d="M3 6l9 7 9-7"/>
        </svg>
        teodoro.vinsquel@brivoterna-example.com
      </li>
      <li>
        <svg viewBox="0 0 24 24" fill="none" stroke="#27aee3" stroke-width="1.8" aria-hidden="true">
          <circle cx="12" cy="12" r="9"/>
          <path d="M3 12h18M12 3c3 3.2 3 14.8 0 18M12 3c-3 3.2-3 14.8 0 18"/>
        </svg>
        www.brivoterna-example.com
      </li>
    </ul>
    <p class="claim">Lantern of the Steady Harvest</p>
    <div class="base-band" aria-hidden="true"><i></i><i></i><i></i></div>
  </section>

</main>
</body>
</html>
```